Website Design for Landscaping/Concrete Company

I need a website that is informative about what my company does and also offers before and after pictures of completed work. I already have a logo. The website must say "FREE ESTIMATES" somewhere and list a phone number. I would like to stick with the logo colors or similar (black and lime green).
Services Offered by Tomlet Builders:
Landscaping
Mowing
Concrete
Sidewalks
Brush Removal
Land Beautification

Please list the company name in large letters TOMLET BUILDERS
and also the contact information in large font.

Right now I am looking for a somewhat coverpage for my website. I don't have a lot of information for people to point and click on yet. Id like to get a coverpage to get my name out and then have a designer come back in a few months and update with more pictures and information.
Updates

If allowed please submit projects after due date. I made a mistake and only posted for one day. Thanks.

Coding

Coded - Design and coding required

```html
<!DOCTYPE html>
<html lang="en">
<head>
<meta charset="utf-8">
<title>Tomlet Builders – Landscaping &amp; Concrete</title>
<link href="https://fonts.googleapis.com/css2?family=Lato:ital,wght@0,400;0,700;0,900;1,400&display=swap" rel="stylesheet">
<style>
:root{
  --lime:#8cc63f;
  --olive:#6f9a1f;
  --black:#000;
  --dark:#1d2117;
  --ink:#222;
  --body:#333;
  --white:#fff;
  --rule:#bbb;
}
*{box-sizing:border-box;margin:0;padding:0}
html,body{width:1200px;height:4615px;overflow:hidden}
body{position:relative;font-family:'Lato',sans-serif;background:var(--white);color:var(--body)}
.abs{position:absolute}
a{text-decoration:none;color:inherit}

/* header */
.site-header{left:0;top:0;width:1200px;height:150px;background:var(--black)}
.brand{left:73px;top:48px;display:flex;align-items:center;gap:10px}
.brand-mark{width:18px;height:18px;background:var(--lime)}
.brand-name{color:var(--lime);font-weight:900;font-size:22px;line-height:1.05;letter-spacing:1px}
.header-phone{left:731px;top:28px;display:flex;align-items:center;gap:12px;color:var(--lime);font-size:23px}
.phone-ring{width:36px;height:36px;border:2px solid var(--lime);border-radius:50%;display:flex;align-items:center;justify-content:center}
.header-cta{left:955px;top:25px;width:170px;height:41px;background:var(--lime);color:var(--white);font-weight:700;font-size:15px;display:flex;align-items:center;justify-content:center}
.main-nav{top:102px;color:var(--white);font-size:17px;font-weight:700}
.main-nav.active{color:var(--lime)}

/* hero */
.hero{left:0;top:150px;width:1200px;height:692px;background:linear-gradient(160deg,#6d6a63 0%,#5b6b3f 35%,#3f6a22 60%,#4b8a25 100%)}
.hero-title{left:73px;top:300px;color:var(--white);font-weight:900;font-size:70px;line-height:66px}
.hero-sub{left:75px;top:446px;color:var(--white);font-weight:700;font-size:31px}
.hero-cta{left:73px;top:519px;width:269px;height:65px;background:var(--lime);color:var(--white);font-weight:900;font-size:25px;display:flex;align-items:center;justify-content:center}

/* section heads */
.section-mark{left:433px;width:334px;height:20px;display:flex;align-items:center;justify-content:space-between}
.section-mark i{display:block;width:90px;height:1px;background:var(--rule)}
.section-mark b{display:block;width:18px;height:18px;background:var(--ink)}
.section-mark.light b{background:var(--white)}
.section-title{left:0;width:1200px;text-align:center;font-weight:900;font-size:28px;color:var(--ink)}
.section-title.light{color:var(--white)}

.copy{font-size:16px;line-height:30.5px;color:var(--body);width:514px}
.btn{background:var(--olive);color:var(--white);font-weight:900;font-size:17px;display:flex;align-items:center;justify-content:center}
.photo{border:0}

/* services */
.services{left:0;top:1455px;width:1200px;height:900px;background:linear-gradient(180deg,#202619,#2c3320 50%,#1e211a)}
.service-card{width:330px;height:245px;border:3px solid var(--white);display:flex;align-items:center;justify-content:center;color:var(--white);font-weight:900;font-size:24px;text-shadow:0 1px 3px rgba(0,0,0,.5)}

/* testimonial */
.testimonial{left:0;top:2977px;width:1200px;height:537px;background:linear-gradient(180deg,#141611,#242a1c)}
.avatar{left:543px;top:3068px;width:114px;height:114px;border-radius:50%;background:radial-gradient(circle,#b07a52,#6d4a30);border:3px solid var(--white)}
.quote-name{left:0;top:3215px;width:1200px;text-align:center;color:var(--lime);font-weight:900;font-size:20px}
.quote{left:120px;top:3254px;width:960px;text-align:center;color:var(--white);font-size:16px;line-height:30.5px}
.dots{left:560px;top:3384px;display:flex;gap:12px}
.dots i{width:10px;height:10px;border-radius:50%;background:var(--white)}
.dots i.on{background:var(--lime)}

/* contact */
.contact-row{left:73px;display:flex;align-items:center;gap:20px;color:var(--ink)}
.contact-icon{width:61px;height:61px;border:2px solid var(--olive);border-radius:50%;display:flex;align-items:center;justify-content:center}
.contact-text{font-size:18px;line-height:25px}
.contact-text.big{font-size:22px;font-weight:700}
.field{left:616px;width:509px;height:57px;border:1px solid #999;padding:18px 22px;font-size:16px;color:#444}

/* footer */
.site-footer{left:0;top:4320px;width:1200px;height:295px;background:var(--black)}
.foot-nav{top:4421px;color:var(--white);font-size:17px;font-weight:700;transform:translateX(-50%)}
.copyright{left:0;top:4472px;width:1200px;text-align:center;color:var(--white);font-size:13px}
.social{top:4505px;width:24px;height:24px;border-radius:50%;background:var(--white)}
</style>
</head>
<body>

<!-- Header -->
<header class="abs site-header"></header>
<div class="abs brand"><span class="brand-mark"></span><span class="brand-name">TOMLET<br>BUILDERS</span></div>
<div class="abs header-phone">
  <span class="phone-ring"><svg width="18" height="18" viewBox="0 0 24 24"><path fill="#8cc63f" d="M6.6 10.8a15.1 15.1 0 0 0 6.6 6.6l2.2-2.2c.3-.3.7-.4 1-.2 1.1.4 2.3.6 3.6.6.6 0 1 .4 1 1V20c0 .6-.4 1-1 1A17 17 0 0 1 3 4c0-.6.4-1 1-1h3.5c.6 0 1 .4 1 1 0 1.3.2 2.5.6 3.6.1.3 0 .7-.2 1z"/></svg></span>
  1800-555-0142
</div>
<a class="abs header-cta">FREE ESTIMATES</a>
<a class="abs main-nav active" style="left:509px">HOME</a>
<a class="abs main-nav" style="left:607px">SERVICES</a>
<a class="abs main-nav" style="left:734px">WHY US</a>
<a class="abs main-nav" style="left:849px">TESTIMONIALS</a>
<a class="abs main-nav" style="left:1021px">CONTACT US</a>

<!-- Hero -->
<section class="abs hero" role="img" aria-label="Photo of a landscaped front yard with lawn, flower beds and a wheelbarrow"></section>
<svg class="abs" style="left:0;top:760px" width="1200" height="90" viewBox="0 0 1200 90"><polygon points="0,82 680,82 1200,10 1200,90 0,90" fill="#fff"/><polygon points="680,82 1200,10 1200,82" fill="#8cc63f"/></svg>
<h1 class="abs hero-title">TOMLET<br>BUILDERS</h1>
<p class="abs hero-sub">We are a Landscaping/Concrete Company</p>
<a class="abs hero-cta">FREE ESTIMATES</a>

<!-- Welcome -->
<div class="abs section-mark" style="top:909px"><i></i><b></b><i></i></div>
<h2 class="abs section-title" style="top:956px">WELCOME TO TOMLET BUILDERS</h2>
<div class="abs photo" style="left:73px;top:1030px;width:513px;height:349px;background:linear-gradient(135deg,#7a9a3a,#4d7a22 50%,#c2a83a)" role="img" aria-label="Photo of a gardener in orange kneeling by shrubs on a lawn"></div>
<p class="abs copy" style="left:616px;top:1020px;width:514px">Sed ut perspiciatis unde omnis iste natus error sit voluptatem accusantium doloremque laudantium, totam rem aperiam, eaque ipsa quae ab illo inventore veritatis et quasi architecto beatae vitae dicta sunt explicabo. Nemo enim ipsam voluptatem quia voluptas sit aspernatur aut odit aut fugit, sed quia consequuntur magni dolores eos qui ratione voluptatem sequi nesciunt. Neque porro quisquam est, qui dolorem ipsum quia dolor sit amet, consectetur, adipisci velit, sed quia non numquam eius modi tempora incidunt ut labore et dolore magnam aliquam quaerat voluptatem.</p>
<a class="abs btn" style="left:616px;top:1320px;width:177px;height:59px">READ MORE</a>

<!-- Services -->
<section class="abs services" role="img" aria-label="Dark background photo of a garden path"></section>
<svg class="abs" style="left:0;top:1455px" width="1200" height="80" viewBox="0 0 1200 80"><polygon points="0,0 0,0 1200,0 0,0" fill="#fff"/><polygon points="0,4 600,28 0,76" fill="#8cc63f"/></svg>
<svg class="abs" style="left:0;top:2272px" width="1200" height="83" viewBox="0 0 1200 83"><polygon points="0,83 600,63 1200,83" fill="#fff"/><polygon points="600,63 1200,2 1200,83" fill="#8cc63f"/></svg>
<div class="abs section-mark light" style="top:1566px"><i></i><b></b><i></i></div>
<h2 class="abs section-title light" style="top:1615px">SERVICES OFFERED BY TOMLET BUILDERS</h2>
<div class="abs service-card" style="left:73px;top:1696px;background:linear-gradient(135deg,#5f9a2a,#2f6a1a)" role="img" aria-label="Photo of a green landscaped garden">LANDSCAPING</div>
<div class="abs service-card" style="left:437px;top:1696px;background:linear-gradient(135deg,#6a4a3a,#4a5a2a)" role="img" aria-label="Photo of a gardener with a cart of plants">MOWING</div>
<div class="abs service-card" style="left:797px;top:1696px;background:linear-gradient(135deg,#8a7a66,#5a4e40)" role="img" aria-label="Photo of fresh concrete being leveled">CONCRETE</div>
<div class="abs service-card" style="left:73px;top:1976px;background:linear-gradient(135deg,#9a9a8a,#4a5a3a)" role="img" aria-label="Photo of a stone sidewalk path">SIDEWALKS</div>
<div class="abs service-card" style="left:437px;top:1976px;background:linear-gradient(135deg,#c06a3a,#6a3a1a)" role="img" aria-label="Photo of a rake clearing leaves">BRUSH REMOVAL</div>
<div class="abs service-card" style="left:797px;top:1976px;background:linear-gradient(135deg,#7a6a5a,#3a5a2a)" role="img" aria-label="Photo of a yard with a white picket fence">LAND BEAUTIFICATION</div>

<!-- Why us -->
<div class="abs section-mark" style="top:2429px"><i></i><b></b><i></i></div>
<h2 class="abs section-title" style="top:2478px">WHY TOMLET BUILDERS?</h2>
<p class="abs copy" style="left:73px;top:2542px">Sed ut perspiciatis unde omnis iste natus error sit voluptatem accusantium doloremque laudantium, totam rem aperiam, eaque ipsa quae ab illo inventore veritatis et quasi architecto beatae vitae dicta sunt explicabo. Nemo enim ipsam voluptatem quia voluptas sit aspernatur aut odit aut fugit, sed quia consequuntur magni dolores eos qui ratione voluptatem sequi nesciunt. Neque porro quisquam est, qui dolorem ipsum quia dolor sit amet, consectetur, adipisci velit, sed quia non numquam eius modi tempora incidunt ut labore et dolore magnam aliquam quaerat voluptatem.</p>
<a class="abs btn" style="left:73px;top:2840px;width:179px;height:60px">READ MORE</a>
<div class="abs photo" style="left:614px;top:2552px;width:513px;height:349px;background:linear-gradient(180deg,#6fa3d8 0%,#8a8a86 45%,#4d7a2a 100%)" role="img" aria-label="Photo of a grey two-storey house with landscaped front garden"></div>

<!-- Testimonial -->
<section class="abs testimonial" role="img" aria-label="Dark background photo of a happy family outdoors"></section>
<svg class="abs" style="left:0;top:2975px" width="1200" height="80" viewBox="0 0 1200 80"><polygon points="0,2 600,30 0,78" fill="#8cc63f"/></svg>
<svg class="abs" style="left:0;top:3434px" width="1200" height="82" viewBox="0 0 1200 82"><polygon points="0,82 600,62 1200,82" fill="#fff"/><polygon points="600,62 1200,4 1200,82" fill="#8cc63f"/></svg>
<div class="abs avatar" role="img" aria-label="Customer portrait"></div>
<p class="abs quote-name">NAME HEADING</p>
<p class="abs quote">“ Sed ut perspiciatis unde omnis iste natus error sit voluptatem &nbsp;accusantium doloremque laudantium, totam rem aperiam, eaque ipsa quae ab illo inventore veritatis et quasi architecto beatae vitae dicta sunt explicabo. Nemo enim ipsam voluptatem quia voluptas sit aspernatur aut odit aut fugit, sed quia consequuntur magni..”</p>
<div class="abs dots"><i class="on"></i><i></i><i></i><i></i></div>

<!-- Contact -->
<div class="abs section-mark" style="top:3575px"><i></i><b></b><i></i></div>
<h2 class="abs section-title" style="top:3624px">CONTACT INFORMATION</h2>
<div class="abs contact-row" style="top:3701px">
  <span class="contact-icon"><svg width="24" height="24" viewBox="0 0 24 24"><path fill="#6f9a1f" d="M12 2a7 7 0 0 0-7 7c0 5.2 7 13 7 13s7-7.8 7-13a7 7 0 0 0-7-7zm0 9.5A2.5 2.5 0 1 1 12 6.5a2.5 2.5 0 0 1 0 5z"/></svg></span>
  <span class="contact-text">Sed ut perspiciatis unde<br>omnis iste natus</span>
</div>
<div class="abs contact-row" style="top:3781px">
  <span class="contact-icon"><svg width="24" height="24" viewBox="0 0 24 24"><path fill="#6f9a1f" d="M6.6 10.8a15.1 15.1 0 0 0 6.6 6.6l2.2-2.2c.3-.3.7-.4 1-.2 1.1.4 2.3.6 3.6.6.6 0 1 .4 1 1V20c0 .6-.4 1-1 1A17 17 0 0 1 3 4c0-.6.4-1 1-1h3.5c.6 0 1 .4 1 1 0 1.3.2 2.5.6 3.6.1.3 0 .7-.2 1z"/></svg></span>
  <span class="contact-text big">1800-555-0142</span>
</div>
<div class="abs contact-row" style="top:3863px">
  <span class="contact-icon"><svg width="24" height="20" viewBox="0 0 24 20"><path fill="#6f9a1f" d="M2 2h20v2l-10 7L2 4zM2 6l10 7 10-7v12H2z"/></svg></span>
  <span class="contact-text big">hello@tomletbuilders.com</span>
</div>
<div class="abs" style="left:73px;top:3954px;width:513px;height:262px;background:linear-gradient(135deg,#e4e8e0,#d6dccd)" role="img" aria-label="Street map showing the company location"></div>
<div class="abs field" style="top:3700px">Name</div>
<div class="abs field" style="top:3772px">Email Address</div>
<div class="abs field" style="top:3843px">Phone No</div>
<div class="abs field" style="top:3915px">Select Services</div>
<div class="abs field" style="top:3985px;height:156px">Message</div>
<a class="abs btn" style="left:616px;top:4157px;width:177px;height:59px">SUBMIT</a>

<!-- Footer -->
<footer class="abs site-footer"></footer>
<svg class="abs" style="left:0;top:4282px" width="1200" height="80" viewBox="0 0 1200 80"><polygon points="0,2 0,76 600,32" fill="#8cc63f"/><polygon points="0,76 600,32 1200,38 1200,38" fill="#000"/></svg>
<a class="abs foot-nav" style="left:317px">HOME</a>
<a class="abs foot-nav" style="left:430px">SERVICES</a>
<a class="abs foot-nav" style="left:550px">WHY US</a>
<a class="abs foot-nav" style="left:693px">TESTIMONIALS</a>
<a class="abs foot-nav" style="left:856px">CONTACT US</a>
<p class="abs copyright">Copyright © 2020 Tomlet Builders All Rights Reserved</p>
<span class="abs social" style="left:475px"></span>
<span class="abs social" style="left:529px"></span>
<span class="abs social" style="left:583px"></span>
<span class="abs social" style="left:644px"></span>
<span class="abs social" style="left:697px"></span>

</body>
</html>
```